The Harlow Reserve Web Site design

I need a web design for my luxury range of Terry Toweling and Spa Accessories for luxury upmarket hotels and Spas. I have a catalog that sets the mood and tone I am looking for. I need a website design that shows off the look and feel of this luxury range while working back to the catalog look and feel. Its all about Upmarket and Luxury. I will be using the website as a reference site and as a site that customers can purchase off.
The Logo is attached as is the catalog. I don't mind changing the color of the Logo to match the website. However I would prefer to keep the font of that logo.

http://thegallerydesk.pixvault-example.com/p504729381
Please can you try and access this link. The Harlow Reserve
Name Greta. Email greta@vellumsupply-example.com.au. Password Harlow.
These images are to be used for shopping page and please use the close up details of texture as background on pages and use those texture details and close ups for banners

Please note the look and feel has to be very upmarket and super luxury. Ficus is on mood and not on retail.
Have a look at the mood on the following websites
Www.gracefulretreats-example.com
And yourcosyseasidecabin-example.com
That one is retail .mi don't want retail focus but it's very clean. And simple and colors are good
Updates

Please rebook brief. I have added some important detail. Thanks

Relook brief. I have added,important detail. Thanks

Target Market(s)

Corporate buyers
This is not for retail selling to consumers
Price it's viewed only after secure login

Industry/Entity Type

Shopping

Colors
acd037
cadf82
fbc995
fce7d3
faa54b

Requirements
Must have
• Luxury. Think luxury. Very high end yet modern like the catalogue
Use banners on home page
Should not have
• Don't use the blue as the main color. It's too cheap.
No products on home page

```html
<!DOCTYPE html>
<html lang="en">
<head>
<meta charset="utf-8">
<title>The Harlow Reserve</title>
<link href="https://fonts.googleapis.com/css2?family=Arimo:wght@400&family=Questrial&family=Source+Sans+3:wght@300;400&display=swap" rel="stylesheet">
<style>
:root{
  --green:#acd037;
  --green-soft:#cadf82;
  --peach:#fbc995;
  --cream:#fdf4ea;
  --orange:#faa54b;
  --backdrop:#ede4da;
  --ink:#222;
  --body:#555;
  --muted:#777;
  --rule:#e6ddd2;
}
*{margin:0;padding:0;box-sizing:border-box}
html,body{width:930px;height:1200px;overflow:hidden}
body{background:var(--backdrop);font-family:"Arimo",Arial,sans-serif;color:var(--body);position:relative}
.page{position:absolute;left:90px;top:0;width:750px;height:1200px;background:var(--cream);box-shadow:0 0 8px rgba(0,0,0,.08)}
.abs{position:absolute}
.topbar{left:0;top:0;width:750px;height:44px;background:var(--green)}
.topbar a{position:absolute;top:18px;font-size:11px;color:#fff;text-decoration:none;letter-spacing:.2px}
.cart{left:636px;top:0;width:64px;height:57px;background:var(--orange);border-radius:0 0 3px 3px;color:#fff;text-align:center;font-size:9px;line-height:10px;padding-top:30px}
.cart svg{position:absolute;left:21px;top:5px}
.totop{left:718px;top:26px}
.logo{left:14px;top:60px;font-family:"Questrial",sans-serif;font-size:21.5px;color:var(--ink)}
.subnav a{position:absolute;top:70px;font-family:"Source Sans 3",sans-serif;font-weight:400;font-size:10px;color:var(--muted);text-decoration:none;letter-spacing:.5px}
.hero{left:0;top:96px;width:750px;height:338px;background:linear-gradient(180deg,#b7b98c 0%,#a9a88a 35%,#9a958a 60%,#c9c1b4 100%)}
.banner{left:224px;top:311px;width:299px;height:93px;background:var(--orange);opacity:.92;color:#fff;font-family:"Source Sans 3",sans-serif;padding:7px 0 0 13px}
.banner .lead{font-size:23px;font-weight:400;line-height:25px}
.banner .big{font-size:55px;font-weight:400;letter-spacing:6px;line-height:56px}
.intro{left:0;top:446px;width:750px;text-align:center;font-family:"Source Sans 3",sans-serif;font-weight:400;font-size:28.5px;line-height:33px;color:var(--ink)}
.mood-label{left:10px;width:146px;height:15px;background:var(--orange);color:#fff;font-size:11px;line-height:15px;padding-left:14px}
.mood{width:171px}
.mood .texture{width:171px;height:99px}
.mood figcaption{margin-top:13px;font-size:9.3px;line-height:14px;color:var(--body)}
.rule{left:10px;top:993px;width:729px;height:1px;background:var(--rule)}
.foot h3{font-weight:400;font-size:13px;color:var(--ink);margin-bottom:10px}
.foot p{font-size:9.3px;line-height:14px;color:var(--body)}
.foot b{font-weight:400;color:var(--ink)}
.thumb{width:33px;height:29px}
.social{left:568px;top:1131px}
</style>
</head>
<body>
<div class="page">
  <nav class="abs topbar">
    <a style="left:11px">HOME</a>
    <a style="left:80px">BATH TOWELS</a>
    <a style="left:194px">ROBES</a>
    <a style="left:269px">ACCESSORIES</a>
    <a style="left:396px">MATS</a>
    <a style="left:480px">POOL</a>
    <a style="left:542px">BEACH</a>
  </nav>
  <div class="abs cart">
    <svg width="22" height="18" viewBox="0 0 22 18" fill="none" stroke="#fff" stroke-width="2"><path d="M6 7 L11 1 L16 7"/><path d="M2 7 H20 L17 17 H5 Z" fill="#fff"/></svg>
    0 ITEM<br>$ 0.00
  </div>
  <svg class="abs totop" width="18" height="10" viewBox="0 0 18 10" fill="none" stroke="#fff" stroke-width="1.3"><path d="M1 9 L9 1 L17 9"/></svg>

  <div class="abs logo">The Harlow Reserve</div>
  <div class="subnav">
    <a style="left:343px">Beach</a>
    <a style="left:402px">Blankets &amp; Throws</a>
    <a style="left:516px">Massage &amp; Sauna</a>
    <a style="left:634px">New Collection</a>
  </div>

  <div class="abs hero" role="img" aria-label="Mood photograph of a bright spa bathroom with green walls, a freestanding bathtub and a window"></div>
  <svg class="abs" style="left:41px;top:297px" width="46" height="46" viewBox="0 0 46 46"><circle cx="23" cy="23" r="23" fill="rgba(255,255,255,.15)"/><path d="M26 15 L19 23 L26 31" stroke="#fff" stroke-width="1.5" fill="none"/></svg>
  <svg class="abs" style="left:663px;top:297px" width="46" height="46" viewBox="0 0 46 46"><circle cx="23" cy="23" r="23" fill="rgba(255,255,255,.15)"/><path d="M20 15 L27 23 L20 31" stroke="#fff" stroke-width="1.5" fill="none"/></svg>
  <div class="abs banner">
    <div class="lead">Wrap Yourself in</div>
    <div class="big">Luxury</div>
  </div>

  <h1 class="abs intro">Here at The Harlow Reserve we deliver the finest in<br>cotton towels, loungewear, and bath accessories</h1>

  <section>
    <h2 class="abs mood-label" style="top:544px;font-weight:400">BLANKETS &amp; THROWS</h2>
    <figure class="abs mood" style="left:10px;top:571px"><div class="texture" role="img" aria-label="Mood close-up of soft white terry with a grey woven edge" style="background:linear-gradient(135deg,#dfe2ea,#9aa0b0)"></div><figcaption>At accusam aliquyam diam diam dolore dolores duo eirmod eos erat, et nonumy sed tempor...</figcaption></figure>
    <figure class="abs mood" style="left:197px;top:571px"><div class="texture" role="img" aria-label="Mood image of layered red and green terry folds" style="background:linear-gradient(180deg,#ad9782,#8b7a5a 50%,#6f8b55)"></div><figcaption>At accusam aliquyam diam diam dolore dolores duo eirmod eos erat, et nonumy sed tempor...</figcaption></figure>
    <figure class="abs mood" style="left:383px;top:571px"><div class="texture" role="img" aria-label="Mood image of plush white folded terry" style="background:linear-gradient(180deg,#a8998a,#e2ddd6 60%,#a8998a)"></div><figcaption>At accusam aliquyam diam diam dolore dolores duo eirmod eos erat, et nonumy sed tempor...</figcaption></figure>
    <figure class="abs mood" style="left:569px;top:571px"><div class="texture" role="img" aria-label="Texture close-up of red and green terry loops" style="background:linear-gradient(160deg,#c46a5a 60%,#7a9058)"></div><figcaption>At accusam aliquyam diam diam dolore dolores duo eirmod eos erat, et nonumy sed tempor...</figcaption></figure>
  </section>

  <section>
    <h2 class="abs mood-label" style="top:777px;font-weight:400">MASSAGE &amp; SAUNA</h2>
    <figure class="abs mood" style="left:10px;top:804px"><div class="texture" role="img" aria-label="Mood close-up of soft white terry with a grey woven edge" style="background:linear-gradient(135deg,#dfe2ea,#9aa0b0)"></div><figcaption>At accusam aliquyam diam diam dolore dolores duo eirmod eos erat, et nonumy sed tempor...</figcaption></figure>
    <figure class="abs mood" style="left:197px;top:804px"><div class="texture" role="img" aria-label="Mood image of layered red and green terry folds" style="background:linear-gradient(180deg,#ad9782,#8b7a5a 50%,#6f8b55)"></div><figcaption>At accusam aliquyam diam diam dolore dolores duo eirmod eos erat, et nonumy sed tempor...</figcaption></figure>
    <figure class="abs mood" style="left:383px;top:804px"><div class="texture" role="img" aria-label="Mood image of plush white folded terry" style="background:linear-gradient(180deg,#a8998a,#e2ddd6 60%,#a8998a)"></div><figcaption>At accusam aliquyam diam diam dolore dolores duo eirmod eos erat, et nonumy sed tempor...</figcaption></figure>
    <figure class="abs mood" style="left:569px;top:804px"><div class="texture" role="img" aria-label="Texture close-up of red and green terry loops" style="background:linear-gradient(160deg,#c46a5a 60%,#7a9058)"></div><figcaption>At accusam aliquyam diam diam dolore dolores duo eirmod eos erat, et nonumy sed tempor...</figcaption></figure>
  </section>

  <div class="abs rule"></div>

  <div class="abs foot" style="left:11px;top:1022px;width:170px">
    <h3>A Few Words About Us</h3>
    <p>At vero eos et accusam et justo duo dolores et ea rebum. Stet clita kasd gubergren, no sea takimata sanctus est Lorem ipsum dolor sit amet. Lorem ipsum dolor sit amet, consetetur sadipscing elitr, sed diam nonumy eirmod tempor invidunt ut labore.</p>
  </div>
  <div class="abs foot" style="left:198px;top:1021px;width:170px">
    <h3>Chirp Updates</h3>
    <p><b>@NorthlaneStudio</b> Free Webdesign Resources everyday, just visit our website.</p>
    <p><b>@NorthlaneStudio</b> Get news and updates abut the webdesigners world at our new blog.</p>
  </div>
  <div class="abs foot" style="left:383px;top:1021px;width:170px">
    <h3>Snapline Gallery</h3>
  </div>
  <div class="abs thumb" style="left:383px;top:1049px;background:linear-gradient(160deg,#c46a5a 60%,#7a9058)" role="img" aria-label="Terry texture"></div>
  <div class="abs thumb" style="left:424px;top:1049px;background:linear-gradient(180deg,#b5a99a,#e6e2dc)" role="img" aria-label="White terry"></div>
  <div class="abs thumb" style="left:466px;top:1049px;background:linear-gradient(180deg,#b05a4e,#6f8b55)" role="img" aria-label="Layered terry"></div>
  <div class="abs thumb" style="left:507px;top:1049px;background:linear-gradient(135deg,#dfe2ea,#7c8294)" role="img" aria-label="Rolled terry"></div>
  <div class="abs thumb" style="left:383px;top:1086px;background:linear-gradient(160deg,#c46a5a 60%,#7a9058)" role="img" aria-label="Terry texture"></div>
  <div class="abs thumb" style="left:424px;top:1086px;background:linear-gradient(180deg,#b5a99a,#e6e2dc)" role="img" aria-label="White terry"></div>
  <div class="abs thumb" style="left:466px;top:1086px;background:linear-gradient(180deg,#b05a4e,#6f8b55)" role="img" aria-label="Layered terry"></div>
  <div class="abs thumb" style="left:507px;top:1086px;background:linear-gradient(135deg,#dfe2ea,#7c8294)" role="img" aria-label="Rolled terry"></div>
  <div class="abs foot" style="left:569px;top:1022px;width:180px">
    <h3>Get In Touch With Us</h3>
    <p>Address: Linden Row 48<br>Phone: +49 555 010 224<br>Fax: +49 555 010 225<br>Email: <b>hello@northlane-example.com</b><br>Web: <b>http://www.northlane-example.com</b></p>
  </div>
  <svg class="abs social" width="140" height="20" viewBox="0 0 140 20" fill="#d6d0c8">
    <circle cx="9" cy="10" r="9"/><circle cx="32" cy="10" r="9"/><circle cx="55" cy="10" r="9"/><circle cx="78" cy="10" r="9"/><circle cx="101" cy="10" r="9"/><circle cx="125" cy="10" r="9"/>
  </svg>
</div>
</body>
</html>
```